Business Card Design

Company is a Commercial Building Company specialising in New Construction and existing refurbishments

Industry/Entity Type

Business

Contact Information for Business Card

Liam Porter
Construction Manager
E Liam@marshbuilding.com.au
M 0400 213 594
Mail 14 Tarrant Rise Harbourvale WA 6170

```html
<!DOCTYPE html>
<html lang="en">
<head>
<meta charset="utf-8">
<title>Marsh Building &amp; Construction – Business Card</title>
<link href="https://fonts.googleapis.com/css2?family=Roboto:wght@400;500;700&display=swap" rel="stylesheet">
<style>
  :root {
    --orange: #f28a22;
    --orange-light: #f5a04a;
    --cyan: #17b6d6;
    --navy: #2b2f45;
    --grey-text: #4a4d5c;
    --paper: #ffffff;
    --backdrop: #e4e2df;
  }
  * { margin: 0; padding: 0; box-sizing: border-box; }
  html, body {
    width: 1200px; height: 997px; overflow: hidden;
    background: var(--backdrop);
    font-family: "Roboto", Arial, sans-serif;
  }
  .sheet {
    position: relative; width: 1200px; height: 997px;
    display: flex; flex-direction: column; align-items: center; justify-content: center; gap: 60px;
  }
  .card {
    position: relative; width: 560px; height: 320px; overflow: hidden;
    box-shadow: 0 6px 18px rgba(0,0,0,0.15);
  }
  /* Front */
  .card-front {
    background: radial-gradient(circle at 50% 40%, var(--orange-light), var(--orange) 75%);
    display: flex; align-items: center; justify-content: center;
  }
  .brand-front {
    display: flex; align-items: center; gap: 16px;
    color: var(--paper); font-weight: 500; text-transform: uppercase;
  }
  .brand-front .brand-square {
    width: 46px; height: 46px; border: 4px solid var(--paper); border-radius: 6px;
  }
  .brand-front .brand-name { font-size: 26px; line-height: 1.15; letter-spacing: 0.5px; }
  /* Back */
  .card-back { background: var(--paper); }
  .card-back .bands { position: absolute; inset: 0; width: 560px; height: 320px; }
  .brand-back {
    position: absolute; left: 34px; top: 42px;
    display: flex; align-items: center; gap: 12px;
    color: var(--navy); font-weight: 500; text-transform: uppercase;
  }
  .brand-back .brand-square { width: 30px; height: 30px; background: var(--cyan); border-radius: 4px; }
  .brand-back .brand-name { font-size: 17px; line-height: 1.15; }
  .rule-orange {
    position: absolute; left: 240px; top: 70px; width: 120px; height: 1px; background: var(--orange);
  }
  .rule-cyan {
    position: absolute; left: 76px; top: 92px; width: 150px; height: 1px; background: var(--cyan);
  }
  .person { position: absolute; right: 34px; top: 40px; text-align: right; }
  .person .name { font-size: 17px; font-weight: 700; color: var(--navy); text-transform: uppercase; letter-spacing: 0.3px; }
  .person .role { font-size: 10.5px; color: var(--grey-text); margin-top: 2px; }
  .address {
    position: absolute; right: 34px; top: 108px; text-align: right;
    font-size: 12px; line-height: 1.45; color: var(--grey-text);
  }
  .contacts {
    position: absolute; left: 34px; top: 200px;
    font-size: 12.5px; color: var(--grey-text); list-style: none;
  }
  .contacts li { display: flex; align-items: center; gap: 10px; line-height: 1.6; }
  .contacts svg { width: 12px; height: 12px; flex: none; }
</style>
</head>
<body>
<main class="sheet">
  <section class="card card-front" aria-label="Card front">
    <div class="brand-front">
      <span class="brand-square"></span>
      <span class="brand-name">Marsh Building<br>&amp; Construction</span>
    </div>
  </section>

  <section class="card card-back" aria-label="Card back">
    <svg class="bands" viewBox="0 0 560 320" aria-hidden="true">
      <polygon points="0,262 396,262 414,240 560,240 560,320 0,320" fill="var(--orange)"/>
      <polygon points="0,270 398,270 432,320 0,320" fill="var(--paper)"/>
      <polygon points="0,275 395,275 425,320 0,320" fill="var(--cyan)"/>
    </svg>
    <div class="brand-back">
      <span class="brand-square"></span>
      <span class="brand-name">Marsh Building<br>&amp; Construction</span>
    </div>
    <div class="rule-orange"></div>
    <div class="rule-cyan"></div>
    <div class="person">
      <p class="name">Liam Porter</p>
      <p class="role">Construction Manager</p>
    </div>
    <p class="address">14 Tarrant Rise<br>Harbourvale WA 6170</p>
    <ul class="contacts">
      <li>
        <svg viewBox="0 0 12 12"><rect x="2" y="1" width="8" height="10" rx="1.5" fill="none" stroke="var(--navy)" stroke-width="1.3"/></svg>
        0400 213 594
      </li>
      <li>
        <svg viewBox="0 0 12 12"><rect x="1" y="2.5" width="10" height="7" fill="none" stroke="var(--navy)" stroke-width="1.2"/><polyline points="1,2.5 6,7 11,2.5" fill="none" stroke="var(--navy)" stroke-width="1.2"/></svg>
        Liam@marshbuilding.com.au
      </li>
    </ul>
  </section>
</main>
</body>
</html>
```